4th Generation Family Business Needs a New Card Design!

We are a family owned 4th Generation company. We are based in the Sydney, Australia area and we are desperately in need of a more modern and classy card. We are monumental masons who design, supply & erect lasting memorials throughout cemeteries in Sydney. Our customers are normally in a period of grieving. I have attached logo files that will need to be implemented on the card. Company was established 1935. Australian Owned and Operated. Card needs to be designed to PIXO.com specification.

Target Market(s)

Our target market is based upon people that a grieving for family members that have passed away. We also deal with alot of companies that own and operate cemeteries.

Industry/Entity Type

Business

Contact Information for Business Card

Simon Harcourt, Operations Manager, 0417293086, simon@harcourtmemorials.com.au
Lewis Harcourt, Director, 0491630572, lewis@harcourtmemorials.com.au
Phone # 02 9561 3048
Website: www.harcourtmemorials.com.au
Address: Suite 17, 8 Palfrey Lane, West Carlow, Sydney NSW 2156

Font styles to use
Serif
Decorative
Script

Requirements
Must have
• Would like to see the logo nicely implemented with a modern design. Embossed lettering would be a nice additive.

```html
<!DOCTYPE html>
<html lang="en">
<head>
<meta charset="utf-8">
<title>Harcourt Memorials – Business Card</title>
<link rel="stylesheet" href="https://fonts.googleapis.com/css2?family=Cinzel:wght@600&family=Libre+Baskerville:ital@0;1&display=swap">
<style>
  :root {
    --backdrop: #3a312d;
    --card-black: #1c1c1e;
    --card-black-light: #2a2a2d;
    --emboss: #303033;
    --gold: #ecbd1f;
    --white: #f4f4f4;
    --swoosh-grey: #8a8a8e;
    --ink: #1d1d1f;
  }
  * { margin: 0; padding: 0; box-sizing: border-box; }
  html, body { width: 1200px; height: 716px; overflow: hidden; }
  body {
    background: var(--backdrop);
    display: flex;
    align-items: center;
    justify-content: center;
    gap: 40px;
  }
  .card {
    position: relative;
    width: 520px;
    height: 300px;
    border-radius: 4px;
    overflow: hidden;
    background: linear-gradient(135deg, var(--card-black-light), var(--card-black) 60%);
  }
  .card-back {
    display: flex;
    align-items: center;
    justify-content: center;
  }
  .brand {
    font-family: "Cinzel", serif;
    font-weight: 600;
    text-align: center;
    line-height: 1.1;
  }
  .card-back .brand { color: var(--emboss); font-size: 40px; }
  .card-back .brand .brand-sub { font-size: 20px; letter-spacing: 6px; }

  .card-front .brand {
    position: absolute;
    left: 38px;
    top: 58px;
    color: var(--white);
    font-size: 30px;
  }
  .card-front .brand .brand-sub { display: block; font-size: 15px; letter-spacing: 5px; }

  .waves { position: absolute; inset: 0; }

  .person {
    position: absolute;
    right: 26px;
    top: 36px;
    text-align: right;
    color: var(--white);
    font-family: "Libre Baskerville", serif;
  }
  .person-name { font-family: "Cinzel", serif; font-weight: 600; font-size: 19px; letter-spacing: 1px; }
  .person-role { font-style: italic; font-size: 11px; margin-bottom: 12px; }
  .person-address { font-size: 12px; line-height: 1.5; }

  .contacts {
    position: absolute;
    right: 22px;
    bottom: 12px;
    list-style: none;
    font-family: "Libre Baskerville", serif;
    font-size: 12px;
    color: var(--ink);
    text-align: right;
    line-height: 15px;
  }
  .contacts li { display: flex; align-items: center; justify-content: flex-end; gap: 7px; }
  .contacts svg { width: 10px; height: 10px; fill: var(--ink); }
</style>
</head>
<body>

  <section class="card card-back">
    <div class="brand">Harcourt<br><span class="brand-sub">Memorials</span></div>
  </section>

  <section class="card card-front">
    <svg class="waves" viewBox="0 0 520 300" aria-hidden="true">
      <path fill="var(--swoosh-grey)" d="M0,140 C130,140 230,192 340,190 C420,188 480,178 520,172 L520,179 C480,185 420,195 340,197 C230,199 130,150 0,150 Z"/>
      <path fill="var(--white)" d="M0,154 C130,154 230,204 340,202 C420,200 480,188 520,183 L520,193 C480,198 420,210 340,212 C230,214 130,168 0,168 Z"/>
      <path fill="var(--gold)" d="M0,174 C120,174 220,226 330,222 C420,219 480,205 520,200 L520,300 L0,300 Z"/>
    </svg>

    <div class="brand">Harcourt<span class="brand-sub">Memorials</span></div>

    <div class="person">
      <p class="person-name">Simon Harcourt</p>
      <p class="person-role">Operations Manager</p>
      <p class="person-address">Suite 17, 8 Palfrey Lane,<br>West Carlow, Sydney NSW 2156</p>
    </div>

    <ul class="contacts">
      <li>0491630572
        <svg viewBox="0 0 10 10"><path d="M2 0h2l1 3-1.5 1a6 6 0 0 0 2.5 2.5L7 5l3 1v2c0 1-1 2-2 2A8 8 0 0 1 0 2c0-1 1-2 2-2z"/></svg></li>
      <li>02 9561 3048
        <svg viewBox="0 0 10 10"><rect x="1" y="3" width="8" height="6" rx="1"/><rect x="0" y="1" width="10" height="2" rx="1"/></svg></li>
      <li>lewis@harcourtmemorials.com.au
        <svg viewBox="0 0 10 10"><path d="M0 2h10v6H0z M0 2l5 3.5L10 2" stroke="#ecbd1f" stroke-width=".8"/></svg></li>
      <li>www.harcourtmemorials.com.au
        <svg viewBox="0 0 10 10"><circle cx="5" cy="5" r="5"/><path d="M0 5h10M5 0v10" stroke="#ecbd1f" stroke-width=".8"/></svg></li>
    </ul>
  </section>

</body>
</html>
```